Boutique Store Selling Antiques and Unique Finds

I need a Web Page designed for my Store Called "Willow Lane". I would like a very classic, muted design that looks European when pulled up. I will be selling Antiques from all over the world and Unique finds that have reproduced. I will also be selling high-end purses and jewelry with unique, reasonable products for the every-day buyer as well.

Target Market(s)

25-70 year old men and women;)

Coding

Coded - Design and coding required

Number of Pages Required

1 page

Colors

Designer to choose only greyscale colors for use in the design.

Requirements
Must have
• I want it

```html
<!DOCTYPE html>
<html lang="en">
<head>
<meta charset="utf-8">
<title>Willow Lane — Antiques and Unique Finds</title>
<link href="https://fonts.googleapis.com/css2?family=Roboto:wght@300;400;500;700&family=Pathway+Gothic+One&display=swap" rel="stylesheet">
<style>
:root{
  --ink:#1c1c1c;
  --dark:#222222;
  --pale:#f2f2f2;
  --paper:#ffffff;
  --line:#d6d6d6;
  --muted:#555555;
  --star:#3a3a3a;
  --photo-light:#cfcfcf;
  --photo-mid:#7a7a7a;
  --photo-deep:#2e2e2e;
}
*{box-sizing:border-box;margin:0;padding:0}
html,body{width:1200px;height:4441px;overflow:hidden}
body{font-family:'Roboto',sans-serif;color:var(--ink);background:var(--paper);position:relative}
.abs{position:absolute}
section,header,nav,footer{width:1200px}

/* top bar */
.topbar{left:0;top:0;width:1200px;height:33px;background:var(--dark);color:#fff;font-size:13px;font-weight:500;line-height:15px}
.topbar .phone{left:145px;top:9px;display:flex;gap:6px;align-items:center}
.topbar .account{right:145px;top:9px;display:flex;gap:14px;align-items:center}
.topbar .account span{display:flex;gap:6px;align-items:center}
.dot{width:10px;height:10px;border-radius:50%;background:#fff;display:inline-block}

/* header */
.masthead{left:0;top:33px;height:105px;background:#fff;border-bottom:1px solid var(--line)}
.search{left:143px;top:30px;width:225px;height:44px;border:1px solid var(--line);font-size:12px;line-height:14px;color:#666;padding:14px 16px}
.search svg{position:absolute;right:14px;top:15px}
.brand{left:0;width:1200px;top:38px;text-align:center;font-size:25px;line-height:30px;letter-spacing:4px;font-weight:500;text-transform:uppercase}
.cart{right:145px;top:36px;display:flex;align-items:center;gap:14px;font-size:14px;font-weight:700}

/* nav */
.mainnav{left:0;top:138px;height:50px;background:var(--pale);border-bottom:1px solid var(--line)}
.mainnav ul{list-style:none;display:flex;gap:38px;position:absolute;left:243px;top:17px;font-size:14px;line-height:16px;font-weight:500}
.mainnav li.active{text-decoration:underline;text-underline-offset:4px}

/* hero */
.hero{left:0;top:188px;height:557px;background:linear-gradient(90deg,#ececec 0%,#dcdcdc 40%,#9c9c9c 75%,#c8c8c8 100%)}
.hero .photo{left:480px;top:0;width:720px;height:557px;background:radial-gradient(ellipse at 55% 45%,#6e6e6e 0%,#4e4e4e 35%,rgba(80,80,80,0) 70%)}
.hero .floor{left:0;bottom:0;width:1200px;height:150px;background:linear-gradient(180deg,rgba(66,66,66,0) 0%,#3d3d3d 100%)}
.hero h1{left:143px;top:108px;font-family:'Pathway Gothic One',sans-serif;font-weight:400;font-size:72px;line-height:72px;color:var(--ink)}
.btn-dark{left:143px;top:281px;width:152px;height:43px;background:var(--ink);color:#fff;font-size:13px;font-weight:700;text-align:center;line-height:43px}
.arrow{width:40px;height:40px;border:2px solid #999;border-radius:50%}
.arrow svg{position:absolute;left:11px;top:11px}

/* section heads */
.sec-title{left:0;width:1200px;text-align:center;font-size:28px;line-height:34px;font-weight:700;text-transform:uppercase}
.mark{left:576px;width:48px;height:2px;background:var(--ink)}

/* shop */
.shop{left:0;top:745px;height:1146px;background:var(--pale)}
.card{background:#fff;border:2px solid var(--line)}
.card .pic{position:absolute;left:8px;top:8px;right:8px;height:324px}
.card .name{position:absolute;left:0;right:0;top:353px;text-align:center;font-size:16px;line-height:20px;font-weight:500}
.card .price{position:absolute;left:0;right:0;top:385px;text-align:center;font-size:17px;line-height:20px}

/* featured */
.featured{left:0;top:1891px;height:690px;background:#fff}
.prod{top:190px;width:215px;height:393px;background:#fff;box-shadow:0 0 8px rgba(0,0,0,.15)}
.prod .pic{position:absolute;left:57px;top:26px;width:100px;height:160px;border-radius:8px}
.prod .price{position:absolute;left:0;right:0;top:214px;text-align:center;font-weight:700;font-size:16px;line-height:20px}
.prod .desc{position:absolute;left:16px;right:16px;top:242px;text-align:center;font-size:14px;line-height:20px;color:var(--muted)}
.prod .add{position:absolute;left:20px;right:20px;top:298px;height:39px;border:2px solid var(--ink);text-align:center;line-height:35px;font-size:12px;font-weight:700}
.prod .stars{position:absolute;left:0;right:0;top:352px;text-align:center;color:var(--star);font-size:14px;line-height:16px;letter-spacing:1px}
.arrow.sm{width:30px;height:30px;border:2px solid #555}
.arrow.sm svg{left:7px;top:7px}

/* newsletter */
.newsletter{left:0;top:2581px;height:441px;background:#262626}
.newsletter .photo{left:560px;top:0;width:640px;height:441px;background:radial-gradient(ellipse at 50% 45%,#8a8a8a 0%,#4a4a4a 40%,#1e1e1e 85%)}
.newsletter .panel{left:0;top:0;width:700px;height:441px;background:#1e1e1e;clip-path:polygon(0 0,100% 0,89% 100%,0 100%)}
.newsletter .logo{left:0;width:720px;top:96px;color:#fff;font-size:22px;line-height:26px;letter-spacing:4px;font-weight:500;text-transform:uppercase;text-align:center}
.newsletter h2{left:0;width:720px;top:138px;color:#fff;font-size:33px;line-height:40px;font-weight:700;text-align:center}
.newsletter p{left:0;width:720px;top:195px;color:#fff;font-size:15px;line-height:24px;text-align:center}
.email{left:138px;top:265px;width:446px;height:52px;border:1px solid #fff;color:#fff;font-size:15px;text-align:center;line-height:50px}
.subscribe{left:138px;top:338px;width:446px;height:52px;background:var(--pale);font-size:16px;font-weight:700;text-align:center;line-height:52px}

/* blog */
.blog{left:0;top:3022px;height:668px;background:var(--pale)}
.post{top:203px;width:443px;height:375px}
.post .pic{position:absolute;left:0;top:0;width:443px;height:268px}
.post .box{position:absolute;left:19px;top:209px;width:404px;height:166px;background:#fff;padding:20px 20px}
.post .meta{font-size:13px;line-height:16px;color:#333;display:flex;gap:28px}
.post .meta span{display:flex;align-items:center;gap:8px}
.post h3{font-size:14px;line-height:18px;font-weight:700;margin-top:14px;text-transform:uppercase}
.post p{font-size:13px;line-height:19px;color:var(--muted);margin-top:12px}

/* promises */
.promises{left:0;top:3690px;height:344px;background:linear-gradient(180deg,#2c2c2c 0%,#383838 50%,#2a2a2a 100%)}
.promise{top:65px;width:330px;text-align:center;color:#fff}
.promise .ring{width:94px;height:94px;border:3px solid #fff;border-radius:50%;margin:0 auto;position:relative}
.promise .ring svg{position:absolute;left:24px;top:24px}
.promise h4{font-size:17px;line-height:20px;font-weight:700;margin-top:26px}
.promise p{font-size:13px;line-height:19px;margin-top:10px;padding:0 20px}

/* footer */
.site-footer{left:0;top:4034px;height:407px;background:var(--pale)}
.site-footer .logo{left:143px;top:98px;width:235px;text-align:center;font-size:20px;line-height:24px;letter-spacing:3px;font-weight:500;text-transform:uppercase}
.social{left:193px;top:148px;display:flex;gap:12px}
.social i{width:30px;height:30px;border:1.5px solid var(--ink);border-radius:50%;display:block}
.fcol h5{font-size:17px;line-height:20px;font-weight:700;margin-bottom:16px}
.fcol li{list-style:none;font-size:13px;line-height:26px;color:#333}
.contact-row{display:flex;gap:14px;font-size:14px;color:#333;line-height:18px;margin-bottom:14px}
.rule{left:143px;top:297px;width:912px;height:1px;background:var(--line)}
.copy{left:143px;top:346px;font-size:15px;line-height:18px}
.pay{left:707px;top:338px;display:flex;gap:12px}
.pay i{width:46px;height:28px;background:#8a8a8a;border-radius:3px;display:block}
</style>
</head>
<body>

<div class="topbar abs">
  <div class="phone abs">
    <svg width="11" height="11" viewBox="0 0 24 24"><path fill="#fff" d="M6.6 10.8a15.1 15.1 0 0 0 6.6 6.6l2.2-2.2c.3-.3.7-.4 1-.2 1.1.4 2.3.6 3.6.6.6 0 1 .4 1 1V20c0 .6-.4 1-1 1A17 17 0 0 1 3 4c0-.6.4-1 1-1h3.5c.6 0 1 .4 1 1 0 1.3.2 2.5.6 3.6.1.3 0 .7-.2 1z"/></svg>
    TOLL FREE : (555)0142-0199
  </div>
  <div class="account abs">
    <span><svg width="11" height="11" viewBox="0 0 24 24"><circle cx="12" cy="7" r="5" fill="#fff"/><path fill="#fff" d="M2 23c0-6 4.5-9 10-9s10 3 10 9z"/></svg>MY ACCOUNT</span>
    <span>|</span>
    <span><svg width="10" height="11" viewBox="0 0 20 24"><rect x="1" y="10" width="18" height="13" fill="#fff"/><path d="M5 10V6a5 5 0 0 1 10 0v4" stroke="#fff" stroke-width="2.5" fill="none"/></svg>LOGIN</span>
    <span><i class="dot"></i><i class="dot"></i><i class="dot"></i></span>
  </div>
</div>

<header class="masthead abs">
  <div class="search abs">Search products...
    <svg width="12" height="12" viewBox="0 0 24 24"><circle cx="10" cy="10" r="7" stroke="#333" stroke-width="3" fill="none"/><path d="M15 15l7 7" stroke="#333" stroke-width="3"/></svg>
  </div>
  <div class="brand abs">Willow Lane</div>
  <div class="cart abs">SHOPPING CART
    <svg width="34" height="32" viewBox="0 0 34 32"><path d="M1 3h5l4 18h17l4-13H9" stroke="#222" stroke-width="2" fill="none"/><circle cx="13" cy="27" r="2.5" fill="#222"/><circle cx="25" cy="27" r="2.5" fill="#222"/><circle cx="30" cy="4" r="4" fill="#777"/></svg>
  </div>
</header>

<nav class="mainnav abs">
  <ul>
    <li class="active">HOME</li><li>ABOUT US</li><li>ANTIQUES</li><li>UNIQUE FINDS</li><li>SHOP ONLINE</li><li>CONTACT US</li>
  </ul>
</nav>

<section class="hero abs">
  <div class="photo abs" role="img" aria-label="Ornate antique crown with jewels on a dark pedestal"></div>
  <div class="floor abs"></div>
  <h1 class="abs">Antiques and<br>Unique Finds</h1>
  <div class="btn-dark abs">SHOP NOW</div>
  <div class="arrow abs" style="left:49px;top:206px"><svg width="14" height="14" viewBox="0 0 14 14"><path d="M9 1L3 7l6 6" stroke="#999" stroke-width="2" fill="none"/></svg></div>
  <div class="arrow abs" style="left:1111px;top:206px"><svg width="14" height="14" viewBox="0 0 14 14"><path d="M5 1l6 6-6 6" stroke="#999" stroke-width="2" fill="none"/></svg></div>
</section>

<section class="shop abs">
  <div class="mark abs" style="top:72px"></div>
  <h2 class="sec-title abs" style="top:104px">From the Shop</h2>
  <div class="card abs" style="left:145px;top:184px;width:526px;height:430px">
    <div class="pic" role="img" aria-label="Star crown resting on a black base" style="background:linear-gradient(180deg,#c4c4c4,#6a6a6a 60%,#262626)"></div>
    <div class="name">Nemo enim ipsam voluptatem quia</div><div class="price">$175.00</div>
  </div>
  <div class="card abs" style="left:690px;top:184px;width:365px;height:430px">
    <div class="pic" role="img" aria-label="Antique gramophone on a round wooden table" style="background:linear-gradient(180deg,#b5b5b5,#888 55%,#5a5a5a)"></div>
    <div class="name">Nemo enim ipsam voluptatem quia</div><div class="price">$175.00</div>
  </div>
  <div class="card abs" style="left:143px;top:638px;width:366px;height:430px">
    <div class="pic" role="img" aria-label="Jewelled crown on a stand" style="background:linear-gradient(180deg,#c8c8c8,#616161 55%,#363636)"></div>
    <div class="name">Nemo enim ipsam voluptatem quia</div><div class="price">$175.00</div>
  </div>
  <div class="card abs" style="left:528px;top:638px;width:527px;height:430px">
    <div class="pic" role="img" aria-label="Engraved antique vases and jugs on a dark background" style="background:radial-gradient(ellipse at 50% 60%,#4a4a4a,#181818 70%)"></div>
    <div class="name">Nemo enim ipsam voluptatem quia</div><div class="price">$175.00</div>
  </div>
</section>

<section class="featured abs">
  <div class="mark abs" style="top:84px"></div>
  <h2 class="sec-title abs" style="top:112px">Featured Products</h2>
  <div class="arrow sm abs" style="left:83px;top:389px"><svg width="12" height="12" viewBox="0 0 12 12"><path d="M8 1L3 6l5 5" stroke="#555" stroke-width="1.5" fill="none"/></svg></div>
  <div class="arrow sm abs" style="left:1085px;top:389px"><svg width="12" height="12" viewBox="0 0 12 12"><path d="M4 1l5 5-5 5" stroke="#555" stroke-width="1.5" fill="none"/></svg></div>

  <div class="prod abs" style="left:143px"><div class="pic" role="img" aria-label="Enamelled cloisonné vase" style="background:linear-gradient(180deg,#a8a8a8,#6e6e6e,#4e4e4e)"></div><div class="price">$ 384.90</div><div class="desc">Nemo enim ipsam voluptatem quia voluptas</div><div class="add">ADD TO CART</div><div class="stars">★★★★★</div></div>
  <div class="prod abs" style="left:375px"><div class="pic" role="img" aria-label="Antique pocket watch" style="background:radial-gradient(circle,#ececec 35%,#5e5e5e 60%,#fff 62%)"></div><div class="price">$ 384.90</div><div class="desc">Nemo enim ipsam voluptatem quia voluptas</div><div class="add">ADD TO CART</div><div class="stars">★★★★★</div></div>
  <div class="prod abs" style="left:607px"><div class="pic" role="img" aria-label="Crown with jewels" style="background:linear-gradient(180deg,#fff 20%,#9a9a9a 40%,#555 70%,#fff 72%)"></div><div class="price">$ 384.90</div><div class="desc">Nemo enim ipsam voluptatem quia voluptas</div><div class="add">ADD TO CART</div><div class="stars">★★★★★</div></div>
  <div class="prod abs" style="left:839px"><div class="pic" role="img" aria-label="Tall painted porcelain vase" style="left:85px;width:45px;background:linear-gradient(180deg,#555,#b5b5b5,#666)"></div><div class="price">$ 384.90</div><div class="desc">Nemo enim ipsam voluptatem quia voluptas</div><div class="add">ADD TO CART</div><div class="stars">★★★★★</div></div>
</section>

<section class="newsletter abs">
  <div class="photo abs" role="img" aria-label="Close view of an ornate crown with a clear gemstone"></div>
  <div class="panel abs"></div>
  <div class="logo abs">Willow Lane</div>
  <h2 class="abs">JOIN OUR NEWSLETTER</h2>
  <p class="abs">Subscribe to our mailing list to receive updates<br>and promotional offers.</p>
  <div class="email abs">Enter your Email</div>
  <div class="subscribe abs">SUBSCRIBE</div>
</section>

<section class="blog abs">
  <div class="mark abs" style="top:98px"></div>
  <h2 class="sec-title abs" style="top:128px">Blog and News</h2>
  <article class="post abs" style="left:143px">
    <div class="pic" role="img" aria-label="Vintage rotary telephone beside dried roses" style="background:linear-gradient(90deg,#7a7a7a,#3e3e3e 55%,#232323)"></div>
    <div class="box">
      <div class="meta"><span><svg width="10" height="10" viewBox="0 0 10 10"><rect x="0" y="1" width="10" height="9" fill="#333"/></svg>9 February 2021</span><span><svg width="10" height="10" viewBox="0 0 10 10"><rect x="0" y="1" width="10" height="9" fill="#333"/></svg>02 Comments</span></div>
      <h3>Nemo enim ipsam voluptatem voluptas sit</h3>
      <p>Sed ut perspiciatis unde omnis iste natus error sit voluptatem accusantium doloremque laudantium, totam rem aperiam, eaque ipsa quae ab illo inventore</p>
    </div>
  </article>
  <article class="post abs" style="left:612px">
    <div class="pic" role="img" aria-label="Room with a gramophone, wooden chair and typewriter" style="background:linear-gradient(180deg,#b2b2b2,#777 60%,#525252)"></div>
    <div class="box">
      <div class="meta"><span><svg width="10" height="10" viewBox="0 0 10 10"><rect x="0" y="1" width="10" height="9" fill="#333"/></svg>9 February 2021</span><span><svg width="10" height="10" viewBox="0 0 10 10"><rect x="0" y="1" width="10" height="9" fill="#333"/></svg>02 Comments</span></div>
      <h3>Nemo enim ipsam voluptatem voluptas sit</h3>
      <p>Sed ut perspiciatis unde omnis iste natus error sit voluptatem accusantium doloremque laudantium, totam rem aperiam, eaque ipsa quae ab illo inventore</p>
    </div>
  </article>
</section>

<section class="promises abs" role="img" aria-label="Dim background of antique ornaments">
  <div class="promise abs" style="left:102px">
    <div class="ring"><svg width="40" height="40" viewBox="0 0 40 40"><rect x="4" y="12" width="20" height="14" fill="#fff"/><path d="M24 16h7l5 5v5H24z" fill="#fff"/><circle cx="11" cy="28" r="3.5" fill="#fff"/><circle cx="30" cy="28" r="3.5" fill="#fff"/></svg></div>
    <h4>FREE SHIPPING ITEM</h4><p>Lorem ipsum dolor sit amet, conctetur adipiscing elit, sed do eiusmod tempor incididunt</p>
  </div>
  <div class="promise abs" style="left:432px">
    <div class="ring"><svg width="40" height="40" viewBox="0 0 40 40"><path d="M4 6h14l18 18-12 12L6 18z" fill="#fff"/><circle cx="11" cy="12" r="2.5" fill="#333"/></svg></div>
    <h4>30 DAYS FREE RETURN</h4><p>Lorem ipsum dolor sit amet, conctetur adipiscing elit, sed do eiusmod tempor incididunt</p>
  </div>
  <div class="promise abs" style="left:759px">
    <div class="ring"><svg width="40" height="40" viewBox="0 0 40 40"><path d="M20 3l14 5v12c0 9-6 14-14 17C12 34 6 29 6 20V8z" fill="#fff"/><path d="M20 9v23c-5-2-8-6-8-12V12z" fill="#333"/></svg></div>
    <h4>OUR GUARANTEE</h4><p>Lorem ipsum dolor sit amet, conctetur adipiscing elit, sed do eiusmod tempor incididunt</p>
  </div>
</section>

<footer class="site-footer abs">
  <div class="logo abs">Willow Lane</div>
  <div class="social abs"><i></i><i></i><i></i></div>
  <div class="fcol abs" style="left:428px;top:58px;width:230px">
    <h5>CONACT US</h5>
    <div class="contact-row"><svg width="14" height="18" viewBox="0 0 14 18"><path d="M7 0a7 7 0 0 1 7 7c0 5-7 11-7 11S0 12 0 7a7 7 0 0 1 7-7z" fill="#222"/><circle cx="7" cy="7" r="2.5" fill="#f2f2f2"/></svg><span>Address;<br>243 Nemo enim ipsam<br>voluptatem quia voluptas</span></div>
    <div class="contact-row"><svg width="16" height="16" viewBox="0 0 24 24"><path fill="#222" d="M6.6 10.8a15.1 15.1 0 0 0 6.6 6.6l2.2-2.2c.3-.3.7-.4 1-.2 1.1.4 2.3.6 3.6.6.6 0 1 .4 1 1V20c0 .6-.4 1-1 1A17 17 0 0 1 3 4c0-.6.4-1 1-1h3.5c.6 0 1 .4 1 1 0 1.3.2 2.5.6 3.6.1.3 0 .7-.2 1z"/></svg><span>(555) 0142 - 0199</span></div>
    <div class="contact-row"><svg width="16" height="12" viewBox="0 0 16 12"><rect width="16" height="12" fill="#222"/><path d="M0 0l8 6 8-6" stroke="#f2f2f2" stroke-width="1.5" fill="none"/></svg><span>info@willowlane.com</span></div>
  </div>
  <div class="fcol abs" style="left:698px;top:58px">
    <h5>QUICK LINKS</h5>
    <ul><li>Home</li><li>About Us</li><li>Antiques</li><li>Unique Find</li><li>Shop online</li><li>Contact Us</li></ul>
  </div>
  <div class="fcol abs" style="left:881px;top:58px">
    <h5>INFORMATION</h5>
    <ul><li>Gift Packs</li><li>Contact Us</li><li>International Shipping Info</li><li>Privacy &amp; Security</li><li>Satisfaction Guarantee</li></ul>
  </div>
  <div class="rule abs"></div>
  <div class="copy abs">© 2021 Willow Lane | All Rights Reserved | Disclaimer</div>
  <div class="pay abs"><i></i><i></i><i></i><i></i><i></i><i></i></div>
</footer>

</body>
</html>
```